Business card design for my company.
I would like the card's background colour to be black. You can also see our web site to get an idea of our brand. https://www.tmwhomecrafting.com.au/
- Name
- Email

```html
<!DOCTYPE html>
<html lang="en">
<head>
<meta charset="utf-8">
<title>TMW Home Crafting – Business Card</title>
<link href="https://fonts.googleapis.com/css2?family=Roboto:wght@400;500;700&display=swap" rel="stylesheet">
<style>
  :root {
    --stage: #2b2b2b;
    --card: #000000;
    --green: #0e9a4a;
    --white: #ffffff;
    --soft: #e9e9e9;
  }
  * { box-sizing: border-box; margin: 0; padding: 0; }
  html, body { width: 1200px; height: 875px; overflow: hidden; }
  body {
    background: var(--stage);
    font-family: "Roboto", Arial, sans-serif;
    position: relative;
  }
  .card {
    position: absolute;
    left: 300px;
    width: 600px;
    height: 343px;
    background: var(--card);
    border-radius: 22px;
    overflow: hidden;
  }
  .card--front { top: 70px; }
  .card--back { top: 462px; }

  .brand {
    display: flex;
    align-items: center;
    gap: 14px;
    color: var(--white);
    font-weight: 700;
    letter-spacing: 1px;
  }
  .brand__mark {
    width: 14px; height: 14px;
    background: var(--green);
    flex: none;
  }
  .card--front .brand {
    position: absolute;
    left: 50%; top: 50%;
    transform: translate(-50%, -50%);
    font-size: 40px;
    white-space: nowrap;
  }
  .card--front .brand__mark { width: 22px; height: 22px; }

  .card--back .brand {
    position: absolute;
    right: 40px; top: 42px;
    font-size: 22px;
    gap: 10px;
  }
  .back__rule {
    position: absolute;
    left: 40px; right: 40px; top: 100px;
    height: 1px;
    background: var(--white);
  }
  .holder {
    position: absolute;
    left: 40px; top: 150px;
  }
  .holder__name {
    color: var(--green);
    font-size: 26px;
    font-weight: 700;
  }
  .holder__role {
    color: var(--white);
    font-size: 15px;
    margin-top: 4px;
  }
  .holder__rule {
    width: 210px; height: 1px;
    background: var(--white);
    margin-top: 12px;
  }
  .contacts {
    list-style: none;
    position: absolute;
    left: 40px; top: 228px;
  }
  .contacts li {
    display: flex;
    align-items: center;
    gap: 10px;
    color: var(--white);
    font-size: 15px;
    height: 22px;
    margin-bottom: 4px;
  }
  .contacts svg { width: 16px; height: 16px; flex: none; }
  .address {
    position: absolute;
    right: 40px; top: 236px;
    text-align: right;
    color: var(--white);
    font-size: 15px;
    line-height: 22px;
  }
  .back__band {
    position: absolute;
    left: 0; bottom: 0;
    width: 600px; height: 14px;
  }
</style>
</head>
<body>
  <section class="card card--front" aria-label="Card front">
    <div class="brand"><span class="brand__mark"></span>TMW Home Crafting</div>
  </section>

  <section class="card card--back" aria-label="Card back">
    <div class="brand"><span class="brand__mark"></span>TMW Home Crafting</div>
    <div class="back__rule"></div>

    <div class="holder">
      <p class="holder__name">Daniel Hartley</p>
      <p class="holder__role">Owner</p>
      <div class="holder__rule"></div>
    </div>

    <ul class="contacts">
      <li>
        <svg viewBox="0 0 16 16" aria-hidden="true"><circle cx="8" cy="8" r="8" fill="var(--green)"/><path d="M5 4.2l1.6-.4 1 2.2-1 .8a5 5 0 0 0 2.6 2.6l.8-1 2.2 1-.4 1.6c-3.6.2-7-3.2-6.8-6.8z" fill="#000"/></svg>
        (407) 555-0142
      </li>
      <li>
        <svg viewBox="0 0 16 16" aria-hidden="true"><rect x="1" y="3.5" width="14" height="9" rx="1" fill="var(--green)"/><path d="M1.5 4l6.5 5 6.5-5" fill="none" stroke="#000" stroke-width="1.2"/></svg>
        info@tmwhomecrafting.com.au
      </li>
      <li>
        <svg viewBox="0 0 16 16" aria-hidden="true"><circle cx="8" cy="8" r="7" fill="var(--green)"/><g fill="none" stroke="#000" stroke-width="1"><ellipse cx="8" cy="8" rx="3" ry="7"/><path d="M1 8h14M2.5 4.5h11M2.5 11.5h11"/></g></svg>
        www.tmwhomecrafting.com.au
      </li>
    </ul>

    <p class="address">421, Address line goes here<br>45452, Country name</p>

    <svg class="back__band" viewBox="0 0 600 14" preserveAspectRatio="none" aria-hidden="true">
      <polygon points="0,4 340,4 352,14 0,14" fill="var(--soft)"/>
      <polygon points="340,0 600,0 600,14 352,14" fill="var(--green)"/>
    </svg>
  </section>
</body>
</html>
```